Women's Uplift & Praise Luncheon - Matching Poster, flyer and Postcard

We are a Christian Event & Travel Company and we are hosting our inaugural event on June 10, 2017. This event is a Women's Uplift & Praise Luncheon aboard a private yacht leaving out of Crescent Landing, Maryland. The event will cater to women who have a vision to start or have already embarked on the journey of starting or growing a business or ministry. The event calls for a matching poster, flyer and postcard design that give an elegant & exquisite feel with just the right breath of freshness. The colors should reflect our logo as this is our launch event. I have also included 2 photos of the Islandsong Heritage Park production (one of our sponsors) - Please include but do not make it take over the design - this is to advertise the door prize. The final design will portray the branding of the company (Christian, travel, events, elegance, professional), the branding of the event (elegant and luxurious) and the importance of this launch event.
Please include the following information:
Lanternway Event & Travel Group presents
Event name: Rising Tide: Grace, Patience & Devotion.
Tag Line/Description: An Exquisite Women's Uplift & Praise Luncheon.
Guest Speaker: Minister Harriet L. Dunmore (Photo included)
VP of Pinecrest Bank
Asst. Pastor & First Lady of Bethany Grove Baptist Church
Special Guest Psalmist: Minister Tasha Bellamy (Photo Included)
Worship Director of Stillmeadow Community Church
Vocalist, Songwriter, Musician, and Clinician
Venue: Aboard the Sovereign Pearl Yacht
Dock: Crescent Landing
512 Marlowe Quay, Fenwick, MD 20999
Boarding 10:00am
Sailing Promptly at 10:30am
(Please be on time the yacht will not wait)
Date: Saturday June 10, 2017
Tickets: Early Bird US$75.00/person (ends May 15, 2017)
Regular Tickets US$95.99
Purchase Tickets at www.lanternwayevent-travel.example/rising-tide
SPACE IS LIMITED DUE TO YACHT CAPACITY
Grand Prize: Vivienne Laroux Purse
Door Prize: 2 Tickets to the Hawaiian Islandsong Heritage Park
Other prizes for special ladies in attendance.
Ladies are asked to dress in Elegant White Ensemble
Corporate Sponsors:
The Islandsong Heritage Park (Logo included)
J. Ramsey Photography (Logo included)
Special Thanks to our Individual Sponsors:
Mrs. L. Garner, Mr. R Fielding & Mr. T. Ogden

Target Market(s)

Women, Business, Ministry, Christians, Middle to Upper Class

Industry/Entity Type

Events

Font styles to use
Serif
Script

Requirements
Must have
• Elegance, professional, vivid in color & font. be creative in Visual and FONT!
• Poster: 18" X 24"
• Flyer: one sided.
• ***** the final design chosen will have a cross referenced design of 1 flyer, 1 postcard 1 poster. This was included so you have a reference - Be creative!!!!!!
Nice to have
• Matching across all 3 designs (poster, flyer & postcard) but sized appropriately and just enough difference to play up the design and be appealing.
• I uploaded 3 example flyers to give you inspiration of the type of visuals I'm looking for. I removed my amateur sample because the designs were copying it instead of being creative.
Should not have
• Any thing inappropriate, alcohol oriented or sexual

```html
<!DOCTYPE html>
<html lang="en">
<head>
<meta charset="utf-8">
<title>Rising Tide – Women's Uplift &amp; Praise Luncheon</title>
<link rel="stylesheet" href="https://fonts.googleapis.com/css2?family=Cinzel:wght@400;700;900&family=Kalam:wght@400&family=Fondamento:ital@0;1&family=Pathway+Gothic+One&family=Tinos:wght@400;700&display=swap">
<style>
  :root{
    --night:#140604;
    --ember:#6a1c0c;
    --rust:#8c2f12;
    --gold:#f5c842;
    --gold-deep:#e0a91f;
    --cream:#f6e8c8;
    --sea:#2a9bb0;
    --sea-deep:#0f5f73;
    --ink:#161616;
    --white:#ffffff;
  }
  *{margin:0;padding:0;box-sizing:border-box}
  html,body{width:900px;height:1200px;overflow:hidden;background:var(--night)}
  .poster{position:relative;width:900px;height:1200px;overflow:hidden;
    background:radial-gradient(ellipse 70% 55% at 50% 38%, var(--rust) 0%, var(--ember) 45%, #2a0a05 80%, var(--night) 100%);}
  .backdrop{position:absolute;inset:0}
  .abs{position:absolute}
  .center{left:0;width:900px;text-align:center}

  .ribbon{position:absolute;left:0;top:0}
  .brand{top:70px;font-family:"Cinzel",serif;font-weight:700;color:var(--gold);font-size:30px;letter-spacing:1px;line-height:1.15}
  .brand small{display:block;font-size:15px;letter-spacing:4px}
  .brand-dot{display:inline-block;width:14px;height:14px;border-radius:50%;background:var(--gold);margin-right:10px;vertical-align:middle}
  .presents{top:182px;font-family:"Fondamento",serif;color:var(--gold);font-size:25px}
  .title{top:208px;font-family:"Cinzel",serif;font-weight:700;color:var(--gold);font-size:70px;letter-spacing:2px;line-height:1;text-shadow:0 2px 3px rgba(0,0,0,.6)}
  .title-rule{left:142px;top:272px;width:658px;height:3px;background:var(--gold)}
  .virtues{right:103px;top:274px;font-family:"Tinos",serif;color:var(--gold);font-size:20px;letter-spacing:.5px}
  .tagline{top:306px;font-family:"Kalam",cursive;color:var(--gold);font-size:33px;line-height:30px}

  .portrait{border:4px solid #050505;border-radius:50%;box-shadow:0 0 10px rgba(0,0,0,.6)}
  .speaker-photo{left:34px;top:340px;width:172px;height:212px;background:linear-gradient(160deg,#7a4a3a,#b0202a 60%,#4a1010)}
  .psalmist-photo{left:701px;top:334px;width:168px;height:212px;background:linear-gradient(160deg,#2a2a2a,#5a4a44 45%,#d8d2c8)}
  .caption{font-family:"Tinos",serif;color:var(--cream);font-size:13.5px;line-height:16.5px;text-align:center}
  .caption b{color:var(--white)}
  .speaker-caption{left:10px;width:225px;top:566px}
  .psalmist-caption{left:670px;width:225px;top:558px}

  .details{font-family:"Fondamento",serif;color:var(--cream);text-align:center;left:200px;width:500px;white-space:nowrap;line-height:1.2}
  .venue{top:394px;font-style:italic;font-size:23px;color:var(--cream)}
  .dock{top:436px;font-size:18px;letter-spacing:.5px}
  .address{top:468px;font-size:18px;font-style:italic}
  .times{top:504px;font-size:24px;font-style:italic;line-height:30px}
  .note{top:568px;font-size:14px;font-style:italic}
  .date{top:608px;font-size:27px;font-style:italic;color:var(--gold)}

  .sea{left:0;top:0}
  .event-photo{border-radius:4px;box-shadow:0 2px 8px rgba(0,0,0,.6)}
  .dance-photo{left:25px;top:713px;width:183px;height:120px;background:linear-gradient(180deg,#3a1a12,#8a5a22 55%,#d8b860)}
  .fire-photo{left:695px;top:713px;width:183px;height:120px;background:radial-gradient(ellipse at 50% 55%,#f08a2a 0%,#7a2a0a 40%,#141010 80%)}

  .sea-text{font-family:"Fondamento",serif;font-style:italic;color:var(--ink);left:0;width:900px;text-align:center;white-space:nowrap}
  .price{font-size:26px}
  .price-note{font-size:14px}
  .buy{font-family:"Pathway Gothic One",sans-serif;font-style:normal;font-size:18px}
  .limit{font-family:"Tinos",serif;font-style:italic;font-size:11px;letter-spacing:1px}
  .prize{font-size:20px;line-height:26px}
  .dress{font-size:21px;letter-spacing:.5px}
  .sponsors-head{font-family:"Cinzel",serif;font-style:normal;font-weight:900;font-size:19px;letter-spacing:3px}
  .sponsor-box{background:var(--white);border-radius:5px;display:flex;align-items:center;justify-content:center;text-align:center;font-family:"Fondamento",serif;color:#8a6a14}
  .sponsor-photo{left:315px;top:1038px;width:85px;height:80px;font-size:12px;line-height:14px;padding:6px}
  .sponsor-park{left:408px;top:1038px;width:173px;height:80px;font-size:18px;line-height:20px;padding:8px}
  .thanks{font-size:22px;line-height:29px}
</style>
</head>
<body>
<main class="poster">
  <svg class="backdrop" width="900" height="1200" role="img" aria-label="Faint dark silhouette of feet stepping onto water, centred behind the text">
    <defs>
      <radialGradient id="shade" cx="50%" cy="45%" r="45%">
        <stop offset="0" stop-color="#1e0703" stop-opacity=".55"/>
        <stop offset="1" stop-color="#1e0703" stop-opacity="0"/>
      </radialGradient>
    </defs>
    <ellipse cx="450" cy="430" rx="260" ry="330" fill="url(#shade)"/>
    <g fill="none" stroke="#b0472a" stroke-opacity=".18" stroke-width="1.5">
      <ellipse cx="450" cy="560" rx="250" ry="120"/>
      <ellipse cx="450" cy="560" rx="340" ry="170"/>
      <ellipse cx="450" cy="560" rx="430" ry="220"/>
    </g>
  </svg>

  <svg class="ribbon" width="200" height="200" aria-hidden="true">
    <polygon points="0,0 175,0 0,175" fill="#1f9ab4"/>
    <polygon points="0,0 118,0 0,118" fill="#0b0b0b"/>
    <text x="72" y="78" transform="rotate(-45 72 78)" text-anchor="middle" font-family="Tinos, serif" font-weight="700" font-size="22" fill="#0b0b0b">Limited Tickets</text>
  </svg>

  <div class="abs center brand"><span class="brand-dot"></span>Lanternway<small>Event &amp; Travel Group</small></div>
  <div class="abs center presents">Presents</div>
  <h1 class="abs center title">RISING TIDE</h1>
  <div class="abs title-rule"></div>
  <div class="abs virtues">GRACE ~ PATIENCE ~ DEVOTION</div>
  <p class="abs center tagline">An Executive Women’s Uplift<br>&amp; Praise Luncheon</p>

  <div class="abs portrait speaker-photo" role="img" aria-label="Portrait photo of guest speaker Harriet L. Dunmore in a red jacket"></div>
  <div class="abs caption speaker-caption">Guest Speaker<br><b>Mstr. Harriet L. Dunmore</b><br>VP of Pinecrest Bank<br>Asst. Pastor &amp; First Lady of<br>Bethany Grove Baptist Church</div>

  <div class="abs portrait psalmist-photo" role="img" aria-label="Portrait photo of psalmist Tasha Bellamy in a white gown"></div>
  <div class="abs caption psalmist-caption">Special Guest Psalmist<br><b>Mstr. Tasha Bellamy</b><br>Worship Director of Stillmeadow<br>Community Church<br>Vocalist, Songwriter, Musician<br>and Clinician</div>

  <div class="abs details venue">Venue : Aboard the Sovereign Pearl Yacht</div>
  <div class="abs details dock">DOCK : CRESCENT LANDING</div>
  <div class="abs details address">512 Marlowe Quay, Fenwick, MD 20999</div>
  <div class="abs details times">Boarding: 10:00 am<br>Sailing Promptly at: 10:30 am</div>
  <div class="abs details note">(Please be on time the yacht will not wait)</div>
  <div class="abs details date">Saturday&nbsp; 10th June 2017</div>

  <svg class="abs sea" width="900" height="1200" aria-hidden="true">
    <defs>
      <linearGradient id="water" x1="0" y1="0" x2="0" y2="1">
        <stop offset="0" stop-color="#3aa8bc"/>
        <stop offset=".45" stop-color="#2a9bb0"/>
        <stop offset="1" stop-color="#0f5f73"/>
      </linearGradient>
    </defs>
    <path d="M0,678 C90,660 170,690 270,676 C380,660 470,690 580,672 C690,655 790,685 900,664 L900,1200 L0,1200 Z" fill="url(#water)"/>
    <g fill="none" stroke="#ffffff" stroke-opacity=".16" stroke-width="1.5">
      <path d="M0,760 C150,745 300,775 450,760 C600,745 750,775 900,758"/>
      <path d="M0,900 C150,885 300,915 450,900 C600,885 750,915 900,898"/>
      <path d="M0,1030 C150,1015 300,1045 450,1030 C600,1015 750,1045 900,1028"/>
      <path d="M0,1150 C150,1135 300,1165 450,1150 C600,1135 750,1165 900,1148"/>
    </g>
  </svg>

  <div class="abs event-photo dance-photo" role="img" aria-label="Photo of island dancers in grass skirts performing on stage"></div>
  <div class="abs event-photo fire-photo" role="img" aria-label="Photo of fire dancers spinning flaming circles at night"></div>

  <div class="abs sea-text price" style="top:688px">Early Bird: $75 /Person</div>
  <div class="abs sea-text price-note" style="top:718px">Early Birds ends 15th May&nbsp; 2017</div>
  <div class="abs sea-text price" style="top:738px">Regular Tickets: $95.99 /Person</div>
  <div class="abs sea-text buy" style="top:775px">Purchase Tickets at www.lanternwayevent-travel.example/rising-tide</div>
  <div class="abs sea-text limit" style="top:801px">SPACE IS LIMITED DUE TO YACHT CAPACITY</div>
  <div class="abs sea-text prize" style="top:825px">Grand Prize: Vivienne Laroux Purse<br>Door Prize: 2 Tickets to the Hawaiian Islandsong Heritage Park<br>Other prizes for special ladies in attendance</div>
  <div class="abs sea-text dress" style="top:925px">Ladies are asked to dress in Elegent White Ensembles</div>
  <div class="abs sea-text dress" style="top:963px">Tickets on Sale&nbsp; 18th March 2017</div>
  <div class="abs sea-text sponsors-head" style="top:1006px">CORPORATE SPONSORS</div>

  <div class="abs sponsor-box sponsor-photo">J. Ramsey Photography</div>
  <div class="abs sponsor-box sponsor-park">Islandsong Heritage Park</div>

  <div class="abs sea-text thanks" style="top:1124px">Special Thanks to our Individual Sponsors<br>Mrs. L. Garner, Mr. R Fielding and Mr. T. Ogden</div>
</main>
</body>
</html>
```